Spring Exterior Painting Advertisement

Attached is the postcard that we used last year(file - pixelharbor_318939...vector....pdf.. The information contained will be the same except for it will be updated for use during the spring of 2023.

The second attachment (sept 2021mailer) is another design that we've used in the past.

```html
<!DOCTYPE html>
<html lang="en">
<head>
<meta charset="utf-8">
<title>Summit Painting – Spring Exterior Postcard</title>
<link rel="stylesheet" href="https://fonts.googleapis.com/css2?family=Libre+Baskerville:wght@400;700&family=Permanent+Marker&display=swap">
<style>
  :root {
    --blue: #0b6aa2;
    --blue-text: #1978b3;
    --gold: #e5a926;
    --ink: #111111;
    --grey-text: #555555;
    --panel: #dcebfa;
    --page: #e9e9e7;
    --white: #ffffff;
    --stamp: #c9c9c9;
    --sky-top: #a9cdee;
    --sky-low: #dde9f3;
    --wall: #8c8f88;
    --grass: #5aa83a;
  }
  * { box-sizing: border-box; margin: 0; padding: 0; }
  html, body { width: 1200px; height: 1200px; overflow: hidden; background: var(--page); }
  .stage {
    position: relative; width: 1932px; height: 1932px;
    transform: scale(0.62112); transform-origin: 0 0;
    font-family: "Libre Baskerville", Georgia, serif; color: var(--ink);
  }
  .card {
    position: absolute; left: 251px; width: 1368px; height: 762px;
    background: var(--white); overflow: hidden;
    box-shadow: 0 3px 8px rgba(0,0,0,.25);
  }
  .card--front { top: 167px; }
  .card--back { top: 1006px; }
  .card-art { position: absolute; inset: 0; width: 100%; height: 100%; }
  .abs { position: absolute; }

  .brand { position: absolute; left: 75px; display: flex; align-items: center; gap: 18px; }
  .brand-name { font-weight: 700; color: var(--ink); line-height: 1; }
  .brand-name .line1 { display: block; font-size: 66px; letter-spacing: 1px; }
  .brand-name .line2 { display: block; font-size: 28px; letter-spacing: 26px; margin-top: 4px; }
  .brand-mark { width: 26px; height: 26px; background: var(--blue-text); }

  .hero { left: 0; top: 290px; width: 470px; text-align: center; color: var(--white); font-weight: 700; }
  .hero .kicker { font-size: 38px; letter-spacing: 1px; }
  .hero .big { font-size: 100px; line-height: 1; margin: 4px 0 6px; }
  .hero .tail { font-size: 37px; }

  .contact { text-align: center; white-space: nowrap; }
  .contact .call { font-size: 32px; letter-spacing: 1px; }
  .contact .phone { font-size: 48px; font-weight: 700; color: var(--blue-text); margin-top: 4px; letter-spacing: 1px; line-height: 1.15; }
  .pill {
    display: inline-block; margin-top: 8px; background: var(--gold); border-radius: 22px;
    font-size: 19px; letter-spacing: 1px; padding: 10px 26px; color: var(--ink);
  }

  .coupon { left: 954px; top: 62px; width: 360px; text-align: center; }
  .coupon .save { font-family: "Permanent Marker", cursive; font-size: 72px; line-height: 1; }
  .coupon .pct { font-family: "Permanent Marker", cursive; font-size: 104px; line-height: .95; }
  .coupon .code { font-size: 26px; letter-spacing: 1px; margin-top: 6px; }
  .coupon .code2 { font-size: 27px; font-weight: 700; letter-spacing: 1px; }
  .coupon .exp { font-size: 15px; letter-spacing: 1px; margin-top: 4px; }

  .quote-head { left: 75px; top: 196px; font-size: 37px; font-weight: 700; color: var(--blue-text); line-height: 1.25; white-space: nowrap; }
  .quote-copy { left: 75px; top: 306px; width: 500px; font-size: 18.5px; line-height: 1.35; color: #222; }
  .services { left: 75px; top: 424px; list-style: none; }
  .services li { display: flex; align-items: center; gap: 20px; height: 46px; font-size: 24px; }
  .services li::before { content: ""; width: 20px; height: 20px; background: var(--blue-text); }

  .return-addr { right: 225px; top: 96px; text-align: right; font-size: 19px; line-height: 1.3; color: var(--grey-text); letter-spacing: 1px; }
  .stamp { left: 1173px; top: 72px; width: 114px; height: 114px; background: var(--stamp); }
</style>
</head>
<body>
<div class="stage">

  <!-- FRONT -->
  <section class="card card--front">
    <svg class="card-art" viewBox="0 0 1368 762">
      <defs>
        <linearGradient id="houseA" x1="0" y1="0" x2="0" y2="1">
          <stop offset="0" stop-color="var(--sky-top)"/>
          <stop offset=".45" stop-color="var(--sky-low)"/>
          <stop offset=".55" stop-color="var(--wall)"/>
          <stop offset=".92" stop-color="#7d8079"/>
          <stop offset=".95" stop-color="var(--grass)"/>
        </linearGradient>
        <linearGradient id="roomA" x1="0" y1="0" x2="0" y2="1">
          <stop offset="0" stop-color="#e8ddc9"/>
          <stop offset=".6" stop-color="#b49a7c"/>
          <stop offset="1" stop-color="#6d4f38"/>
        </linearGradient>
      </defs>
      <path d="M0 245 L570 240 L520 330 L470 505 L0 505 Z" fill="var(--blue)"/>
      <path d="M600 195 C700 110 820 90 1368 100 L1368 762 L590 762 C545 640 545 420 600 195 Z" fill="var(--blue)"/>
      <path d="M610 210 C710 130 820 110 1368 120 L1368 762 L600 762 C562 640 562 420 610 210 Z" fill="url(#houseA)" role="img" aria-label="Photo of a grey two-storey house with a front porch and green lawn"/>
      <path d="M560 255 L608 195 L585 270 Z" fill="var(--gold)"/>
      <path d="M790 70 C870 48 940 45 1000 52 L985 62 C930 58 870 62 800 78 Z" fill="var(--gold)"/>
      <circle cx="753" cy="211" r="140" fill="var(--white)"/>
      <circle cx="753" cy="211" r="130" fill="url(#roomA)" role="img" aria-label="Photo of a bright living room with a stone fireplace"/>
      <circle cx="1134" cy="204" r="182" fill="var(--gold)"/>
    </svg>

    <div class="brand" style="top:86px">
      <div class="brand-name"><span class="line1">SUMMIT</span><span class="line2">PAINTING</span></div>
      <span class="brand-mark"></span>
    </div>

    <div class="hero abs">
      <div class="kicker">EXTERIOR JOB?</div>
      <div class="big">GET IT</div>
      <div class="tail">PAINTED NOW!</div>
    </div>

    <div class="contact abs" style="left:10px; top:555px; width:460px;">
      <div class="call">CALL US TODAY!</div>
      <div class="phone">(555) 014-2286</div>
      <div class="pill">WWW.SUMMITPAINTINGCO.COM</div>
    </div>

    <div class="coupon abs">
      <div class="save">SAVE</div>
      <div class="pct">15%</div>
      <div class="code">COUPON CODE</div>
      <div class="code2">'EXT2023'</div>
      <div class="exp">EXPIRES15.05.2023</div>
    </div>
  </section>

  <!-- BACK -->
  <section class="card card--back">
    <svg class="card-art" viewBox="0 0 1368 762">
      <defs>
        <linearGradient id="houseB" x1="0" y1="0" x2="0" y2="1">
          <stop offset="0" stop-color="#f4f6f5"/>
          <stop offset=".3" stop-color="#b9a99a"/>
          <stop offset=".45" stop-color="#d8c79e"/>
          <stop offset=".9" stop-color="#c9b68d"/>
          <stop offset=".94" stop-color="var(--grass)"/>
        </linearGradient>
        <linearGradient id="roomB" x1="0" y1="0" x2="0" y2="1">
          <stop offset="0" stop-color="#f1ede6"/>
          <stop offset=".6" stop-color="#c8bba8"/>
          <stop offset="1" stop-color="#6a5240"/>
        </linearGradient>
      </defs>
      <path d="M0 0 L560 0 C720 150 760 420 640 620 C590 700 520 740 420 762 L0 762 Z" fill="var(--panel)"/>
      <path d="M530 0 L560 0 C740 120 770 440 650 640 C600 710 540 748 470 762 L380 762 C520 730 620 650 660 520 C720 340 680 140 530 0 Z" fill="var(--blue)"/>
      <path d="M0 718 C120 738 300 725 520 688 L505 722 C330 752 140 762 0 762 Z" fill="var(--gold)"/>
      <path d="M670 0 L705 0 L728 40 Z" fill="var(--gold)"/>
      <path d="M760 440 C900 400 1100 400 1368 400 L1368 762 L690 762 C700 640 720 520 760 440 Z" fill="url(#houseB)" role="img" aria-label="Photo of a beige two-storey colonial house with white trim"/>
      <circle cx="709" cy="179" r="140" fill="var(--white)"/>
      <circle cx="709" cy="179" r="130" fill="url(#roomB)" role="img" aria-label="Photo of a furnished living room with fireplace and armchairs"/>
    </svg>

    <div class="brand" style="top:72px">
      <div class="brand-name"><span class="line1">SUMMIT</span><span class="line2">PAINTING</span></div>
      <span class="brand-mark"></span>
    </div>

    <div class="quote-head abs">REQUEST YOUR<br>FREE SUMMIT QUOTE</div>
    <p class="quote-copy abs">Summit painting's local team offers professional painting for your home's exterior &amp; interior surfaces. With over 19 years in business, we offer skillful workmanship backed by a three-year warranty.</p>

    <ul class="services abs">
      <li>PRESSURE WASHING</li>
      <li>EXTERIOR PAINTING &amp; STAINING</li>
      <li>CARPENTRY</li>
      <li>INTERIOR PAINTING</li>
      <li>CABINETRY FINISHING</li>
      <li>COLOR CONSULATAIONS</li>
    </ul>

    <div class="return-addr abs">Summit Painting<br>118 Harbor Lane Suite B<br>Millbrook, WI 53000</div>
    <div class="stamp abs"></div>

    <div class="contact abs" style="left:840px; top:240px; width:450px;">
      <div class="call">CALL US TODAY!</div>
      <div class="phone">(555) 014-2286</div>
      <div class="pill">WWW.SUMMITPAINTINGCO.COM</div>
    </div>
  </section>

</div>
</body>
</html>
```